KLV Plant Services

We are a heavy diesel mechanical business with additional air con certificates, remapping engine rebuilt

Contact Information for Business Card

Company Name, Director Name, Managing Director, Contact details, email and website

Font styles to use
Serif
Script

```html
<!DOCTYPE html>
<html lang="en">
<head>
<meta charset="utf-8">
<title>KLV Plant Services – Business Card</title>
<link rel="stylesheet" href="https://fonts.googleapis.com/css2?family=Poppins:wght@400;500;700;800&display=swap">
<style>
  :root {
    --backdrop: #2b2b2b;
    --navy: #1c1c78;
    --card-white: #ffffff;
    --card-black: #151515;
    --mark-black: #222222;
    --ink: #1a1a1a;
  }
  * { box-sizing: border-box; margin: 0; padding: 0; }
  html, body { width: 1200px; height: 881px; overflow: hidden; }
  body {
    background: var(--backdrop);
    font-family: "Poppins", sans-serif;
    display: flex;
    align-items: center;
    justify-content: center;
    gap: 40px;
  }
  .card {
    position: relative;
    width: 540px;
    height: 309px;
    border-radius: 22px;
    box-shadow: 0 5px 0 var(--navy), 0 14px 30px rgba(0,0,0,.55);
    overflow: hidden;
  }
  .card--back {
    background: var(--card-black);
    display: flex;
    align-items: center;
    justify-content: center;
  }
  .back-mark {
    display: flex;
    align-items: center;
    gap: 10px;
    font-weight: 800;
    font-size: 26px;
    color: var(--mark-black);
  }
  .back-mark .dot {
    width: 26px; height: 26px; border-radius: 50%;
    background: var(--mark-black);
  }
  .card--front { background: var(--card-white); }
  .brand {
    position: absolute;
    right: 36px;
    top: 52px;
    display: flex;
    align-items: center;
    gap: 10px;
    font-weight: 800;
    font-size: 25px;
    color: var(--navy);
  }
  .brand .dot {
    width: 30px; height: 30px; border-radius: 50%;
    background: var(--ink);
  }
  .rule-long {
    position: absolute;
    left: 40px; right: 36px; top: 126px;
    height: 2px; background: var(--navy);
  }
  .person { position: absolute; left: 40px; top: 142px; }
  .person__name {
    font-weight: 800; font-size: 24px; letter-spacing: .5px;
    color: var(--navy); text-transform: uppercase; line-height: 1.1;
  }
  .person__role { font-size: 13px; color: var(--ink); margin-top: 2px; }
  .rule-short {
    position: absolute; left: 40px; top: 198px;
    width: 230px; height: 2px; background: var(--navy);
  }
  .contact {
    position: absolute; left: 40px; top: 208px;
    font-size: 13px; color: var(--ink); line-height: 1.3;
  }
  .contact__address { margin-bottom: 4px; }
  .contact__row { display: flex; align-items: center; gap: 8px; }
  .contact__row svg { width: 12px; height: 12px; flex: none; }
  .website {
    position: absolute; right: 36px; top: 146px;
    font-size: 12px; font-weight: 500; letter-spacing: 1.5px;
    color: var(--navy);
  }
</style>
</head>
<body>
  <section class="card card--back">
    <div class="back-mark"><span class="dot"></span>KLV Plant Services</div>
  </section>

  <section class="card card--front">
    <div class="brand"><span class="dot"></span>KLV Plant Services</div>
    <div class="rule-long"></div>
    <div class="website">www.klvplantservices.com</div>
    <div class="person">
      <div class="person__name">Mark Delaney</div>
      <div class="person__role">Director</div>
    </div>
    <div class="rule-short"></div>
    <div class="contact">
      <div class="contact__address">2750 Harlan Ridge Rd<br>Millbrook, GA 30099</div>
      <div class="contact__row">
        <svg viewBox="0 0 24 24" aria-hidden="true"><path fill="#1c1c78" d="M6.6 10.8a15 15 0 0 0 6.6 6.6l2.2-2.2a1 1 0 0 1 1-.25 11.4 11.4 0 0 0 3.6.57 1 1 0 0 1 1 1V20a1 1 0 0 1-1 1A17 17 0 0 1 3 4a1 1 0 0 1 1-1h3.5a1 1 0 0 1 1 1c0 1.25.2 2.45.57 3.57a1 1 0 0 1-.25 1z"/></svg>
        <span>470-555-0182</span>
      </div>
      <div class="contact__row">
        <svg viewBox="0 0 24 24" aria-hidden="true"><rect x="2.5" y="5" width="19" height="14" rx="2" fill="none" stroke="#1c1c78" stroke-width="2.2"/><path d="M3 6l9 7 9-7" fill="none" stroke="#1c1c78" stroke-width="2.2"/></svg>
        <span>info@klvplantservices.com</span>
      </div>
    </div>
  </section>
</body>
</html>
```